Meadow Kr Circle (company name is Meadow Kr Circle LLP)

management of homestay, hospitality something similar with https://www.dorvika.example

Target Market(s)

johor bahru market (Malaysia)

Contact Information for Business Card

Meadow Circle KR LLP

Logo Text

eyes catching, attractive, amazing, Nice, jaw dropping for design

Coding

Coded - Design and coding required

Number of Pages Required

5+ page

Colors

Designer to choose colors to be used in the design.

Requirements
Must have
• please change the short term proposal to our company logo and change the name from dorvika to meadow KR Circle LLP
• thanks
Nice to have
• please let me have eyes catching , jaw dropping design

```html
<!DOCTYPE html>
<html lang="en">
<head>
<meta charset="utf-8">
<title>Meadow Kr Circle – Short-Stay Management</title>
<link href="https://fonts.googleapis.com/css2?family=Montserrat:wght@400;500;600;700&display=swap" rel="stylesheet">
<style>
:root{
  --green:#5a7a1c;
  --green-dark:#47611a;
  --blue:#1c56a8;
  --ink:#222;
  --muted:#555;
  --grey-bg:#efefef;
  --black:#050505;
  --white:#fff;
  --star:#e98a12;
}
*{box-sizing:border-box;margin:0;padding:0}
html,body{width:1200px;height:4255px;overflow:hidden}
body{position:relative;font-family:'Montserrat',sans-serif;color:var(--ink);background:var(--white)}
.abs{position:absolute}
.brand{display:flex;align-items:center;gap:10px;font-weight:700;color:var(--green);font-size:30px}
.brand .mark{width:44px;height:44px;background:var(--blue);display:block}

/* header */
.site-header{left:0;top:0;width:1200px;height:86px;background:var(--white);box-shadow:0 2px 6px rgba(0,0,0,.08);z-index:3}
.site-header .brand{position:absolute;left:110px;top:20px}
.nav{position:absolute;right:60px;top:32px;display:flex;gap:34px;font-size:16px;color:#444;align-items:center}
.nav .active{color:var(--green);font-weight:600}

/* hero */
.hero{left:0;top:86px;width:1200px;height:710px;background:linear-gradient(180deg,#1b2738 0%,#2f3f52 40%,#6a5038 72%,#2e3a2a 100%)}
.hero-title{left:0;width:1200px;top:315px;text-align:center;color:var(--white)}
.hero-title .name{display:inline-flex;align-items:center;gap:16px;font-size:72px;font-weight:700}
.hero-title .name .mark{width:70px;height:70px;border:4px solid var(--white);display:block}
.hero-sub{left:0;width:1200px;top:422px;text-align:center;color:var(--white);font-size:41px;font-weight:500}
.hero-tag{left:0;width:1200px;top:497px;text-align:center;color:var(--white);font-size:29px;font-weight:500}
.hero-dots{left:1132px;top:400px;display:flex;flex-direction:column;gap:10px;align-items:center}
.hero-dots span{width:10px;height:10px;border-radius:50%;background:var(--white)}
.hero-dots span.on{width:16px;height:16px;border:3px solid var(--white);background:transparent}

/* about */
.about-brand{left:113px;top:918px}
.about-photo{left:550px;top:875px;width:540px;height:375px;background:linear-gradient(135deg,#c9c4bb,#8b8478 55%,#3c3a3a);box-shadow:0 8px 24px rgba(0,0,0,.25)}
.about-card{left:117px;top:1010px;width:490px;height:362px;border:3px solid var(--green);background:var(--white);padding:70px 80px 0 38px}
.about-card h2{font-size:34px;font-weight:600;margin-bottom:18px}
.about-card p{font-size:13px;line-height:1.9;color:var(--muted);text-align:justify}

/* services */
.services-band{left:0;top:1470px;width:1200px;height:325px;background:linear-gradient(180deg,#5f8121,#4c6c18)}
.section-title{left:0;width:1200px;text-align:center;font-size:40px;font-weight:600}
.services-title{top:1528px;color:var(--white);font-size:34px}
.service-card{top:1628px;width:316px;height:362px;background:var(--white);box-shadow:0 4px 14px rgba(0,0,0,.18);padding:10px;text-align:center}
.service-card .pic{width:296px;height:162px}
.service-card h3{font-size:20px;font-weight:500;margin:26px 0 12px;line-height:1.35}
.service-card p{font-size:14px;line-height:1.75;color:var(--muted);padding:0 18px}

/* steps */
.steps-title{top:2100px;font-size:36px}
.steps-sub{left:0;width:1200px;top:2166px;text-align:center;font-size:15px;line-height:1.85;color:var(--muted)}
.step{top:2278px;width:240px;text-align:center}
.step .ring{width:166px;height:166px;margin:0 auto;border-radius:50%;background:var(--white);box-shadow:0 2px 12px rgba(0,0,0,.14);position:relative}
.step .num{position:absolute;left:50%;top:-20px;transform:translateX(-50%);width:64px;height:64px;border-radius:50%;background:var(--blue);color:var(--white);font-size:26px;font-weight:700;display:flex;align-items:center;justify-content:center}
.step .ring svg{position:absolute;left:53px;top:68px}
.step h4{margin-top:36px;font-size:20px;font-weight:500;line-height:1.5}

/* packages */
.packages-band{left:0;top:2625px;width:1200px;height:655px;background:var(--grey-bg)}
.packages-title{top:2685px;font-size:40px}
.pkg{background:var(--white);box-shadow:0 4px 14px rgba(0,0,0,.15)}
.pkg-head{position:absolute;left:0;top:0;width:100%;color:var(--white);font-weight:600;font-size:21px;text-align:center;display:flex;align-items:center;justify-content:center;line-height:1.3}
.pkg ul{list-style:none;position:absolute;left:26px;right:12px}
.pkg li{font-size:11.5px;color:#444;display:flex;gap:9px;align-items:flex-start;line-height:1.45;margin-bottom:8px}
.pkg li svg{flex:none;margin-top:2px}
.pkg-foot{position:absolute;left:0;bottom:0;width:100%;height:50px;display:flex}
.pkg-foot .paid{flex:1;background:#e9e9e1;display:flex;align-items:center;padding-left:44px;font-size:16px;font-weight:500}
.pkg-foot .price{width:128px;display:flex;align-items:center;justify-content:center;color:var(--white);font-weight:600;font-size:17px}

/* testimonials */
.testi-title{top:3340px;font-size:42px;font-weight:500}
.testi{top:3485px;width:296px;height:168px;background:var(--white);border-radius:8px;box-shadow:0 3px 14px rgba(0,0,0,.16);padding:58px 18px 0;text-align:center;font-size:13px;line-height:1.85;color:var(--muted)}
.avatar{width:86px;height:86px;border-radius:50%;border:4px solid var(--white);box-shadow:0 2px 8px rgba(0,0,0,.2);background:linear-gradient(160deg,#d9b79d,#7a5a47)}
.testi-name{top:3694px;width:296px;text-align:center;color:var(--green);font-size:16px;font-weight:500}
.stars{top:3722px;width:296px;text-align:center;color:var(--star);font-size:17px;letter-spacing:3px}

/* footer */
.footer{left:0;top:3880px;width:1200px;height:375px;background:var(--black);color:var(--white)}
.footer h5{position:absolute;top:50px;font-size:20px;font-weight:600}
.footer .col{position:absolute;top:102px;font-size:14px;line-height:2.1}
.contact-line{display:flex;gap:20px;align-items:flex-start;font-size:15px;line-height:1.75;font-weight:500}
.socials{display:flex;gap:12px}
.socials span{width:26px;height:26px;background:var(--white);display:block}
.news-text{font-size:14px;line-height:1.75;font-weight:600;width:270px}
.news-input{width:266px;height:36px;background:var(--white);color:#777;font-size:12px;display:flex;align-items:center;padding-left:10px;margin-top:14px}
.news-btn{width:266px;height:38px;background:var(--blue);color:var(--white);display:flex;align-items:center;justify-content:center;font-weight:600;font-size:16px;margin-top:8px}
.copyright{position:absolute;left:0;top:325px;width:1200px;text-align:center;font-size:14px;font-weight:500}
</style>
</head>
<body>

<header class="abs site-header">
  <div class="brand"><span class="mark"></span>Meadow Kr Circle</div>
  <nav class="nav">
    <span class="active">Home</span><span>About Us</span><span>How To Start?</span><span>Packages</span><span>Contact Us</span>
    <svg width="18" height="18" viewBox="0 0 18 18"><circle cx="7" cy="7" r="5.5" fill="none" stroke="#5a7a1c" stroke-width="2"/><path d="M11 11l6 6" stroke="#5a7a1c" stroke-width="2.4"/></svg>
  </nav>
</header>

<section class="abs hero" role="img" aria-label="Modern villa with lit windows and a pool at dusk"></section>
<div class="abs hero-title"><span class="name"><span class="mark"></span>Meadow Kr Circle</span></div>
<div class="abs hero-sub">Short-Stay Management Proposal</div>
<div class="abs hero-tag">Maximize Your Rental Income</div>
<div class="abs hero-dots"><span class="on"></span><span></span><span></span></div>
<svg class="abs" style="left:0;top:680px" width="1200" height="120" viewBox="0 0 1200 120">
  <path d="M0 62 Q420 40 1200 0 V60 Q600 110 0 120Z" fill="#5a7a1c"/>
  <path d="M0 92 Q600 60 1200 46 V120 H0Z" fill="#fff"/>
</svg>

<section>
  <div class="abs brand about-brand"><span class="mark"></span>Meadow Kr Circle</div>
  <div class="abs about-card">
    <h2>About Us</h2>
    <p>We are a short-term rental management and provides hospitality services to help property owners maximize their rental income. Our goal is to help you reap the most from your rental income without you having to do any of the hard work such as handle all the particular renting problems on StayNest, RoomHarbor, cleaning and dealing with tenants and guests.</p>
  </div>
  <div class="abs about-photo" role="img" aria-label="Consultant meeting a couple at a table"></div>
</section>

<section>
  <div class="abs services-band"></div>
  <h2 class="abs section-title services-title">Our Hassle-Free Full Hospitality Service</h2>
  <div class="abs service-card" style="left:113px">
    <div class="pic" role="img" aria-label="Two businessmen shaking hands" style="background:linear-gradient(135deg,#c8d3de,#5d6e82)"></div>
    <h3>Answering Enquiries,<br>Check-Ins / Outs</h3>
    <p>We will answer all guest's enquiries, meet them to handover key and verification check. We also provide 24hr on-call support.</p>
  </div>
  <div class="abs service-card" style="left:443px">
    <div class="pic" role="img" aria-label="Smiling staff member in an office with bookshelves" style="background:linear-gradient(135deg,#b59a7c,#6b5646)"></div>
    <h3>Cleaning, Laundry and<br>Maintenance</h3>
    <p>We get the professional cleaning team to clean up the place after the guest checked-out every time.</p>
  </div>
  <div class="abs service-card" style="left:773px">
    <div class="pic" role="img" aria-label="Hands working on a tablet and paperwork" style="background:linear-gradient(135deg,#e4e0da,#9d968e)"></div>
    <h3>Marketing and<br>Optimization</h3>
    <p>We take professional photos and write persuasive copywriting to optimize your listing in order to get more booking.</p>
  </div>
</section>

<section>
  <h2 class="abs section-title steps-title">How To Start?</h2>
  <p class="abs steps-sub">The following steps are required in order to get<br>your place ready to start.</p>
  <div class="abs step" style="left:125px">
    <div class="ring"><span class="num">01</span>
      <svg width="60" height="56" viewBox="0 0 60 56" fill="none" stroke="#1c56a8" stroke-width="2.5"><path d="M6 26L30 6l24 20"/><path d="M12 22v30h36V22"/><rect x="18" y="30" width="10" height="10"/><rect x="32" y="30" width="10" height="10"/></svg>
    </div>
    <h4>Getting The Required<br>Items</h4>
  </div>
  <div class="abs step" style="left:365px">
    <div class="ring"><span class="num">02</span>
      <svg width="60" height="56" viewBox="0 0 60 56" fill="none" stroke="#1c56a8" stroke-width="2.5"><path d="M4 28L30 6l26 22"/><path d="M12 22v30h36V22"/><path d="M25 52V36h10v16"/></svg>
    </div>
    <h4>Renovation &amp;<br>Furnishing</h4>
  </div>
  <div class="abs step" style="left:605px">
    <div class="ring"><span class="num">03</span>
      <svg width="60" height="56" viewBox="0 0 60 56" fill="none" stroke="#1c56a8" stroke-width="2.5"><rect x="14" y="6" width="32" height="42" rx="2"/><path d="M20 16h20M20 24h20M20 32h14"/><path d="M34 40l4 4 8-9"/></svg>
    </div>
    <h4>Sign A Management<br>Agreement</h4>
  </div>
  <div class="abs step" style="left:857px">
    <div class="ring"><span class="num">04</span>
      <svg width="60" height="56" viewBox="0 0 60 56" fill="none" stroke="#1c56a8" stroke-width="2.5"><circle cx="38" cy="16" r="10"/><path d="M31 23L10 48M14 43l6 6M19 37l5 5"/></svg>
    </div>
    <h4>Handover Keys &amp;<br>Access Cards, And<br>Relevant Information</h4>
  </div>
</section>

<section>
  <div class="abs packages-band"></div>
  <h2 class="abs section-title packages-title">Our Packages</h2>

  <div class="abs pkg" style="left:177px;top:2796px;width:265px;height:362px">
    <div class="pkg-head" style="height:78px;background:var(--green);clip-path:polygon(0 0,100% 0,100% 78%,50% 100%,0 78%)">Economic Package</div>
    <ul style="top:108px">
      <li><svg width="14" height="12" viewBox="0 0 14 12"><path d="M1 6l4 4 8-9" fill="none" stroke="#5a7a1c" stroke-width="2.6"/></svg>Full Height Day &amp; Night curtain</li>
      <li><svg width="14" height="12" viewBox="0 0 14 12"><path d="M1 6l4 4 8-9" fill="none" stroke="#5a7a1c" stroke-width="2.6"/></svg>Main Entrance Door Grill</li>
      <li><svg width="14" height="12" viewBox="0 0 14 12"><path d="M1 6l4 4 8-9" fill="none" stroke="#5a7a1c" stroke-width="2.6"/></svg>Supply &amp; Install LED Surface Light</li>
      <li><svg width="14" height="12" viewBox="0 0 14 12"><path d="M1 6l4 4 8-9" fill="none" stroke="#5a7a1c" stroke-width="2.6"/></svg>Supply &amp; Install Down Light</li>
      <li><svg width="14" height="12" viewBox="0 0 14 12"><path d="M1 6l4 4 8-9" fill="none" stroke="#5a7a1c" stroke-width="2.6"/></svg>Supply &amp; Install Ceiling Fan</li>
      <li><svg width="14" height="12" viewBox="0 0 14 12"><path d="M1 6l4 4 8-9" fill="none" stroke="#5a7a1c" stroke-width="2.6"/></svg>Retractive Hanging Rack</li>
    </ul>
    <div class="pkg-foot"><span class="paid">Paid</span><span class="price" style="background:var(--green)">RM7,950.00</span></div>
  </div>

  <div class="abs pkg" style="left:467px;top:2772px;width:266px;height:410px">
    <div class="pkg-head" style="height:94px;background:var(--blue);clip-path:polygon(0 0,100% 0,100% 78%,50% 100%,0 78%);padding-bottom:12px">Furniture Package</div>
    <ul style="top:126px">
      <li><svg width="14" height="12" viewBox="0 0 14 12"><path d="M1 6l4 4 8-9" fill="none" stroke="#1c56a8" stroke-width="2.6"/></svg>Sofa bed</li>
      <li><svg width="14" height="12" viewBox="0 0 14 12"><path d="M1 6l4 4 8-9" fill="none" stroke="#1c56a8" stroke-width="2.6"/></svg>Coffee table</li>
      <li><svg width="14" height="12" viewBox="0 0 14 12"><path d="M1 6l4 4 8-9" fill="none" stroke="#1c56a8" stroke-width="2.6"/></svg>Dining table set with 6-seaters</li>
      <li><svg width="14" height="12" viewBox="0 0 14 12"><path d="M1 6l4 4 8-9" fill="none" stroke="#1c56a8" stroke-width="2.6"/></svg>Ironing board</li>
      <li><svg width="14" height="12" viewBox="0 0 14 12"><path d="M1 6l4 4 8-9" fill="none" stroke="#1c56a8" stroke-width="2.6"/></svg>Microfiber pillows</li>
      <li><svg width="14" height="12" viewBox="0 0 14 12"><path d="M1 6l4 4 8-9" fill="none" stroke="#1c56a8" stroke-width="2.6"/></svg>Carpet rug</li>
    </ul>
    <div class="pkg-foot"><span class="paid" style="background:#fff;padding-left:44px">Paid</span><span class="price" style="background:var(--blue);width:136px">RM9,900.00</span></div>
  </div>

  <div class="abs pkg" style="left:758px;top:2796px;width:265px;height:362px">
    <div class="pkg-head" style="height:78px;background:var(--green);clip-path:polygon(0 0,100% 0,100% 78%,50% 100%,0 78%);padding-bottom:8px">Curtain, Soft touch<br>&amp; MISC</div>
    <ul style="top:108px">
      <li><svg width="14" height="12" viewBox="0 0 14 12"><path d="M1 6l4 4 8-9" fill="none" stroke="#5a7a1c" stroke-width="2.6"/></svg>Bed linens x 3 sets</li>
      <li><svg width="14" height="12" viewBox="0 0 14 12"><path d="M1 6l4 4 8-9" fill="none" stroke="#5a7a1c" stroke-width="2.6"/></svg>Cooking utensils, Cutlery and Kitchenware</li>
      <li><svg width="14" height="12" viewBox="0 0 14 12"><path d="M1 6l4 4 8-9" fill="none" stroke="#5a7a1c" stroke-width="2.6"/></svg>Designer standing lamp</li>
      <li><svg width="14" height="12" viewBox="0 0 14 12"><path d="M1 6l4 4 8-9" fill="none" stroke="#5a7a1c" stroke-width="2.6"/></svg>Power saving cut-off system</li>
      <li><svg width="14" height="12" viewBox="0 0 14 12"><path d="M1 6l4 4 8-9" fill="none" stroke="#5a7a1c" stroke-width="2.6"/></svg>Bathroom linens and accessories</li>
    </ul>
    <div class="pkg-foot"><span class="paid">Paid</span><span class="price" style="background:var(--green)">RM4,500.00</span></div>
  </div>
</section>

<section>
  <h2 class="abs section-title testi-title">Testimonials</h2>
  <div class="abs testi" style="left:117px">Lorem ipsum dolor sit amet, consectetur adipiscing elit, sed do eiusmod tempor incididunt ut</div>
  <div class="abs testi" style="left:452px">Lorem ipsum dolor sit amet, consectetur adipiscing elit, sed do eiusmod tempor incididunt ut</div>
  <div class="abs testi" style="left:784px">Lorem ipsum dolor sit amet, consectetur adipiscing elit, sed do eiusmod tempor incididunt ut</div>
  <div class="abs avatar" style="left:221px;top:3426px" role="img" aria-label="Portrait of client Lena Ashgrove"></div>
  <div class="abs avatar" style="left:556px;top:3426px" role="img" aria-label="Portrait of client Marisa Joy Delano"></div>
  <div class="abs avatar" style="left:888px;top:3426px;background:linear-gradient(160deg,#c9b09a,#3f4a5a)" role="img" aria-label="Portrait of client Owen Barlett"></div>
  <div class="abs testi-name" style="left:117px">Lena Ashgrove</div>
  <div class="abs testi-name" style="left:452px">Marisa Joy Delano</div>
  <div class="abs testi-name" style="left:784px">Owen Barlett</div>
  <div class="abs stars" style="left:117px">★★★★★</div>
  <div class="abs stars" style="left:452px">★★★★★</div>
  <div class="abs stars" style="left:784px">★★★★★</div>
</section>

<svg class="abs" style="left:0;top:3790px" width="1200" height="92" viewBox="0 0 1200 92">
  <path d="M0 62 Q500 40 1200 0 V92 H0Z" fill="#5a7a1c"/>
  <path d="M0 82 Q600 60 1200 40 V92 H0Z" fill="#050505"/>
</svg>

<footer class="abs footer">
  <h5 style="left:110px">Contact Us</h5>
  <div class="col" style="left:110px;top:98px">
    <div class="contact-line"><svg width="20" height="26" viewBox="0 0 20 26"><path d="M10 1a8 8 0 0 0-8 8c0 6 8 16 8 16s8-10 8-16a8 8 0 0 0-8-8z" fill="#fff"/><circle cx="10" cy="9" r="3" fill="#050505"/></svg><span>L12-04 Riverlight Suites, Jalan<br>Seri Alam, Taman Pelangi,<br>80400 Johor Bahru.</span></div>
    <div class="contact-line" style="margin-top:18px;align-items:center"><svg width="22" height="20" viewBox="0 0 22 20" fill="none" stroke="#fff" stroke-width="2.4"><path d="M3 12V10a8 8 0 0 1 16 0v2"/><rect x="2" y="11" width="4" height="7" fill="#fff"/><rect x="16" y="11" width="4" height="7" fill="#fff"/></svg><span>+65 5550 1842</span></div>
    <div class="socials" style="margin-top:24px"><span></span><span></span><span></span><span></span></div>
  </div>
  <h5 style="left:415px">Quick Links</h5>
  <div class="col" style="left:420px">Home<br>About Us<br>How To Start?<br>Packages<br>Contact Us</div>
  <h5 style="left:612px">Other Links</h5>
  <div class="col" style="left:615px;top:100px;line-height:2">Privacy Policy<br>Terms &amp; Conditions</div>
  <h5 style="left:818px">Newsletter</h5>
  <div class="col" style="left:818px;top:100px">
    <p class="news-text">But I must explain to you how all this mistaken idea of denouncing pleasure and praising.</p>
    <div class="news-input">Enter your email address</div>
    <div class="news-btn">Subscribe</div>
  </div>
  <p class="copyright">© 2018 Copyrights | All Rights Reserved</p>
</footer>

</body>
</html>
```